SloPitch Ad

Looking for a creative eye-catching ad to go on the front page of my website to promote a softball league. Ad dimensions needs to be 1194 by 624, or in that ratio so that it can also be used on facebook.
I have attached some graphics that I have seen on other sites that I like for general ideas. Will need the colors to match with my website (www.kdrplayzone.com) but logo is not necessary

```html
<!DOCTYPE html>
<html lang="en">
<head>
<meta charset="utf-8">
<title>Softball Leagues Now Open</title>
<link rel="stylesheet" href="https://fonts.googleapis.com/css2?family=Montserrat:wght@500;600;700&display=swap">
<style>
  :root {
    --night: #0d1210;
    --field-dark: #2e3a1c;
    --field: #56662e;
    --infield: #a4643a;
    --band-green: #6fae45;
    --band-white: #f1f1ef;
    --ink: #232323;
    --stripe-yellow: #f3d64a;
    --button-top: #79c11f;
    --button-bottom: #3f9a0b;
    --white: #ffffff;
  }
  * { margin: 0; padding: 0; box-sizing: border-box; }
  html, body { width: 1200px; height: 627px; overflow: hidden; background: var(--night); }
  .ad {
    position: relative;
    width: 1200px;
    height: 627px;
    overflow: hidden;
    font-family: "Montserrat", sans-serif;
  }
  .stadium-photo {
    position: absolute;
    inset: 0;
    background:
      radial-gradient(ellipse 330px 130px at 760px 300px, rgba(164,100,58,0.85), rgba(164,100,58,0) 75%),
      radial-gradient(ellipse 900px 260px at 520px 330px, rgba(86,102,46,0.9), rgba(46,58,28,0) 80%),
      linear-gradient(180deg, var(--night) 0%, #1a1c16 30%, var(--field-dark) 50%, var(--field) 70%, var(--field-dark) 100%);
  }
  .bands { position: absolute; inset: 0; }
  .headline {
    position: absolute;
    left: 84px;
    top: 102px;
    color: var(--white);
    line-height: 1;
  }
  .headline-top {
    display: block;
    font-size: 50px;
    font-weight: 600;
    letter-spacing: 0.5px;
  }
  .headline-main {
    display: block;
    margin-top: 12px;
    font-size: 86px;
    font-weight: 600;
    letter-spacing: 1px;
  }
  .register-button {
    position: absolute;
    left: 86px;
    top: 260px;
    width: 316px;
    height: 43px;
    background: linear-gradient(180deg, var(--button-top), var(--button-bottom));
    color: var(--white);
    font-size: 21px;
    font-weight: 500;
    display: flex;
    align-items: center;
    justify-content: center;
  }
  .band-text {
    position: absolute;
    left: 0;
    width: 1200px;
    text-align: center;
    transform: rotate(-3.3deg);
    font-weight: 700;
    line-height: 1;
  }
  .band-text--kicker { top: 396px; font-size: 27px; color: var(--ink); }
  .band-text--title { top: 462px; font-size: 52px; color: var(--ink); font-weight: 600; }
  .band-text--brand { top: 542px; font-size: 32px; color: var(--white); font-weight: 600; }
</style>
</head>
<body>
<main class="ad">
  <div class="stadium-photo" role="img" aria-label="Night photo of a lit softball stadium with players on the field"></div>

  <svg class="bands" width="1200" height="627" viewBox="0 0 1200 627" aria-hidden="true">
    <polygon points="0,626 1200,530 1200,627 0,627" fill="rgba(8,10,8,0.7)"/>
    <polygon points="0,545 1200,475 1200,535 0,630" fill="rgba(10,12,10,0.55)"/>
    <polygon points="0,426 1200,354 1200,404 0,472" fill="var(--band-green)"/>
    <polygon points="0,472 1200,404 1200,476 0,546" fill="var(--band-white)"/>
    <g stroke-linecap="butt">
      <line x1="0" y1="596" x2="490" y2="563" stroke="var(--stripe-yellow)" stroke-width="6"/>
      <line x1="700" y1="546" x2="1200" y2="510" stroke="var(--stripe-yellow)" stroke-width="6"/>
      <line x1="0" y1="586" x2="490" y2="553" stroke="var(--white)" stroke-width="2"/>
      <line x1="700" y1="537" x2="1200" y2="501" stroke="var(--white)" stroke-width="2"/>
      <line x1="0" y1="606" x2="490" y2="573" stroke="var(--white)" stroke-width="1.5"/>
      <line x1="700" y1="556" x2="1200" y2="520" stroke="var(--stripe-yellow)" stroke-width="2"/>
    </g>
  </svg>

  <h1 class="headline">
    <span class="headline-top">SOFTBALL&nbsp; LEAGUES</span>
    <span class="headline-main">NOW OPEN</span>
  </h1>

  <div class="register-button">Register now</div>

  <p class="band-text band-text--kicker">Lets Play</p>
  <p class="band-text band-text--title">Softball league</p>
  <p class="band-text band-text--brand">KDR Play Zone</p>
</main>
</body>
</html>
```